BUSINESS CARD DESIGN

NAME- DALE VORSKIN
PHONE NUMER - 555- 714-9082
EMAIL- OFFICE@TRV-GROUNDMAKRZ.COM
BACK OF CARD- SPEACIALIZES IN LAND CLEARING, FORESTRY MUCLHING AND EXCAVATION

Contact Information for Business Card

NAME- DALE VORSKIN PHONE NUMER - 555- 714-9082 EMAIL- OFFICE@TRV-GROUNDMAKRZ.COM BACK OF CARD- SPEACIALIZES IN LAND CLEARING , MUCLHING AND EXCAVATION

```html
<!DOCTYPE html>
<html lang="en">
<head>
<meta charset="utf-8">
<title>Terravale Groundmakrz – Business Card</title>
<link rel="stylesheet" href="https://fonts.googleapis.com/css2?family=Michroma&family=Roboto:wght@400;500&display=swap">
<style>
  :root {
    --stage: #141414;
    --card: #262626;
    --card-deep: #1f1f1f;
    --gold: #f7b500;
    --edge: #ff9f0a;
    --white: #f2f2f2;
    --faint: #2e2e2e;
  }
  * { margin: 0; padding: 0; box-sizing: border-box; }
  html, body { width: 1200px; height: 840px; overflow: hidden; background: var(--stage); }
  .stage { position: relative; width: 1200px; height: 840px; }

  .card {
    position: absolute;
    width: 620px; height: 354px;
    background: linear-gradient(135deg, var(--card) 0%, var(--card-deep) 100%);
    border-radius: 28px;
    border-bottom: 5px solid var(--edge);
    border-left: 2px solid var(--gold);
    overflow: hidden;
    box-shadow: 0 18px 40px rgba(0,0,0,.55);
  }
  .card--back { left: 60px; top: 50px; }
  .card--front { left: 520px; top: 432px; }

  .brand-name {
    font-family: "Michroma", sans-serif;
    color: var(--gold);
    font-size: 15px;
    letter-spacing: 1px;
    line-height: 1.3;
    text-align: center;
    white-space: nowrap;
  }
  .brand-name__line { display: block; }
  .brand-rule { height: 2px; background: var(--gold); margin-top: 6px; }

  /* back */
  .back-brand { position: absolute; right: 46px; top: 34px; width: 240px; }
  .back-mark {
    position: absolute; left: 40px; top: 70px;
    width: 300px; height: 300px; border-radius: 50%;
    background: radial-gradient(circle at 40% 35%, #333 0%, var(--faint) 60%, #222 100%);
  }
  .specialties { position: absolute; right: 46px; top: 140px; text-align: right; }
  .specialties__title {
    font-family: "Roboto", sans-serif; font-weight: 500;
    color: var(--gold); font-size: 20px; margin-bottom: 8px;
  }
  .specialties__item {
    font-family: "Roboto", sans-serif; color: var(--white);
    font-size: 18px; line-height: 1.4; list-style: none;
  }
  .specialties__item::after {
    content: ""; display: inline-block; width: 7px; height: 7px;
    border-radius: 50%; background: var(--gold); margin-left: 10px; vertical-align: middle;
  }

  /* front */
  .front-brand { position: absolute; right: 40px; top: 28px; width: 240px; text-align: center; }
  .front-brand__dot {
    width: 60px; height: 60px; border-radius: 50%;
    background: var(--gold); margin: 0 auto 10px;
  }
  .front-brand__phone {
    font-family: "Michroma", sans-serif; color: var(--gold);
    font-size: 10px; letter-spacing: 5px; margin-top: 6px;
  }
  .person { position: absolute; left: 40px; bottom: 40px; width: 540px; }
  .person__name {
    font-family: "Michroma", sans-serif; color: var(--gold);
    font-size: 26px; line-height: 1.3; letter-spacing: 1px; margin-bottom: 8px;
  }
  .person__rule { height: 1px; background: var(--white); margin-bottom: 14px; }
  .contact { list-style: none; }
  .contact__item {
    display: flex; align-items: center; gap: 10px;
    font-family: "Roboto", sans-serif; color: var(--white);
    font-size: 19px; line-height: 1.45;
  }
  .contact__icon { width: 18px; height: 18px; flex: none; }
</style>
</head>
<body>
<main class="stage">

  <section class="card card--back" aria-label="Card back">
    <div class="back-brand">
      <div class="brand-name"><span class="brand-name__line">TERRAVALE</span><span class="brand-name__line">GROUNDMAKRZ LLC</span></div>
      <div class="brand-rule"></div>
    </div>
    <div class="back-mark" aria-hidden="true"></div>
    <div class="specialties">
      <p class="specialties__title">SPEACIALIZES IN</p>
      <ul>
        <li class="specialties__item">LAND CLEARING</li>
        <li class="specialties__item">MUCLHING</li>
        <li class="specialties__item">EXCAVATION</li>
      </ul>
    </div>
  </section>

  <section class="card card--front" aria-label="Card front">
    <div class="front-brand">
      <div class="front-brand__dot" aria-hidden="true"></div>
      <div class="brand-name"><span class="brand-name__line">TERRAVALE</span><span class="brand-name__line">GROUNDMAKRZ LLC</span></div>
      <div class="brand-rule"></div>
      <div class="front-brand__phone">555-714-9082</div>
    </div>
    <div class="person">
      <h1 class="person__name">DALE VORSKIN</h1>
      <div class="person__rule"></div>
      <ul class="contact">
        <li class="contact__item">
          <svg class="contact__icon" viewBox="0 0 24 24" aria-hidden="true"><path fill="#f7b500" d="M6.6 10.8a15 15 0 0 0 6.6 6.6l2.2-2.2a1 1 0 0 1 1-.25 11.4 11.4 0 0 0 3.6.57 1 1 0 0 1 1 1V20a1 1 0 0 1-1 1A17 17 0 0 1 3 4a1 1 0 0 1 1-1h3.5a1 1 0 0 1 1 1c0 1.25.2 2.45.57 3.57a1 1 0 0 1-.25 1z"/></svg>
          555- 714-9082
        </li>
        <li class="contact__item">
          <svg class="contact__icon" viewBox="0 0 24 24" aria-hidden="true"><path fill="#f7b500" d="M3 5h18a1 1 0 0 1 1 1v12a1 1 0 0 1-1 1H3a1 1 0 0 1-1-1V6a1 1 0 0 1 1-1zm9 7.5L4 7.2V8l8 5.3L20 8v-.8z"/></svg>
          office@trv-groundmakrz.com
        </li>
      </ul>
    </div>
  </section>

</main>
</body>
</html>
```